Harborline Auto LLC

Car Dealer Customer Service
Address: 2874 Cresthaven Road, Shelbyville, TN 37162
web: www.harborlineautoxq.net
email: harborlineautoxq@mailnest.example
Phone: (931) 555-0148
Phone: (629) 555-0173

```html
<!DOCTYPE html>
<html lang="en">
<head>
<meta charset="utf-8">
<title>Harborline Auto – Business Card</title>
<link rel="stylesheet" href="https://fonts.googleapis.com/css2?family=Montserrat:wght@700&family=Arimo:wght@400&family=Oswald:wght@500&display=swap">
<style>
  :root {
    --backdrop: #2b2b2d;
    --card: #1e1f21;
    --card-back-a: #0d0d0e;
    --card-back-b: #3a3a3c;
    --brand-blue: #1f8ed0;
    --brand-gold: #f2b33d;
    --text-light: #ffffff;
    --rule: #6a6a6c;
  }
  * { box-sizing: border-box; margin: 0; padding: 0; }
  html, body { width: 1200px; height: 1108px; overflow: hidden; }
  body {
    background: var(--backdrop);
    position: relative;
    font-family: "Arimo", Arial, sans-serif;
  }
  .card {
    position: absolute;
    top: 174px;
    width: 470px;
    height: 760px;
    border-radius: 28px;
    overflow: hidden;
  }
  .card-front {
    left: 90px;
    background: var(--card);
    text-align: center;
    padding-top: 88px;
  }
  .card-back { left: 640px; background: var(--card-back-a); }

  .brand-dot {
    width: 92px; height: 92px;
    border-radius: 50%;
    background: var(--brand-blue);
    margin: 0 auto 26px;
  }
  .brand-name {
    font-family: "Montserrat", sans-serif;
    font-weight: 700;
    font-size: 40px;
    color: var(--brand-blue);
    letter-spacing: 0.5px;
  }
  .person-name {
    margin-top: 74px;
    font-family: "Montserrat", sans-serif;
    font-weight: 700;
    font-size: 28px;
    color: var(--brand-blue);
  }
  .person-title {
    font-size: 22px;
    color: var(--brand-gold);
    margin-top: 2px;
  }
  .icon-row {
    display: flex;
    align-items: center;
    justify-content: center;
    gap: 8px;
    margin-top: 18px;
  }
  .icon-row .rule { width: 42px; height: 1px; background: var(--rule); margin: 0 6px; }
  .icon {
    width: 38px; height: 38px;
    background: var(--brand-blue);
    border-radius: 4px;
    display: flex; align-items: center; justify-content: center;
  }
  .contact-list {
    list-style: none;
    margin-top: 16px;
    font-size: 22px;
    line-height: 30px;
    color: var(--text-light);
  }
  .contact-list .accent { color: var(--brand-blue); }
  .contact-list .email { font-size: 19px; }
  .divider { width: 300px; height: 1px; background: var(--rule); margin: 18px auto; }
  .address { font-size: 22px; line-height: 30px; color: var(--text-light); font-style: normal; }

  .back-pattern {
    position: absolute; inset: 0;
    background: linear-gradient(160deg, var(--card-back-b) 0%, #1a1a1b 45%, var(--card-back-a) 100%);
  }
  .back-mark {
    position: absolute;
    left: 310px; top: 430px;
    width: 64px; height: 64px;
    border-radius: 50%;
    background: var(--brand-blue);
  }
  .tagline {
    position: absolute;
    left: 0; right: 0; bottom: 118px;
    text-align: center;
    font-family: "Oswald", sans-serif;
    font-weight: 500;
    font-size: 34px;
    letter-spacing: 1px;
    color: var(--brand-blue);
    text-transform: uppercase;
  }
</style>
</head>
<body>
  <section class="card card-front">
    <div class="brand-dot"></div>
    <div class="brand-name">HARBORLINE AUTO</div>

    <div class="person-name">DANIEL REYES</div>
    <div class="person-title">Managing Director</div>

    <div class="icon-row">
      <span class="rule"></span>
      <span class="icon"><svg width="22" height="22" viewBox="0 0 24 24"><path fill="#fff" d="M6.6 10.8a15 15 0 0 0 6.6 6.6l2.2-2.2c.3-.3.7-.4 1-.2 1.1.4 2.3.6 3.6.6.6 0 1 .4 1 1V20c0 .6-.4 1-1 1A17 17 0 0 1 3 4c0-.6.4-1 1-1h3.5c.6 0 1 .4 1 1 0 1.3.2 2.5.6 3.6.1.3 0 .7-.2 1z"/></svg></span>
      <span class="icon"><svg width="22" height="22" viewBox="0 0 24 24"><path fill="#fff" d="M6.6 10.8a15 15 0 0 0 6.6 6.6l2.2-2.2c.3-.3.7-.4 1-.2 1.1.4 2.3.6 3.6.6.6 0 1 .4 1 1V20c0 .6-.4 1-1 1A17 17 0 0 1 3 4c0-.6.4-1 1-1h3.5c.6 0 1 .4 1 1 0 1.3.2 2.5.6 3.6.1.3 0 .7-.2 1z"/></svg></span>
      <span class="icon"><svg width="22" height="22" viewBox="0 0 24 24" fill="none" stroke="#fff" stroke-width="2"><circle cx="12" cy="12" r="9"/><ellipse cx="12" cy="12" rx="4" ry="9"/><path d="M3 12h18"/></svg></span>
      <span class="icon"><svg width="22" height="22" viewBox="0 0 24 24" fill="none" stroke="#fff" stroke-width="2"><rect x="3" y="6" width="18" height="12"/><path d="M3 6l9 7 9-7"/></svg></span>
      <span class="rule"></span>
    </div>

    <ul class="contact-list">
      <li>(931) 555-0148</li>
      <li>(629) 555-0173</li>
      <li>www.<span class="accent">harborlineautoxq</span>.net</li>
      <li class="email">harborlineautoxq@mailnest.example</li>
    </ul>
    <div class="divider"></div>
    <address class="address">2874 Cresthaven Road<br>Shelbyville, TN 37162</address>
  </section>

  <section class="card card-back">
    <div class="back-pattern" role="img" aria-label="Glossy repeating pattern of the brand emblem across the card back"></div>
    <div class="back-mark"></div>
    <div class="tagline">Car Dealer Customer Service</div>
  </section>
</body>
</html>
```